New Fun, Positive, energised looking Business Card Needed for High Achiever Coach

I am looking for a two sided full colour business card. I am self employed and have recently re branded my 1-2-1 work re-vitalising high achievers. My target client base for these cards is therefore high achievers - usually aged 40 -55, they are often entrepreneurs, CEO or work in banking and finance and 2/3 are male. I work with them on 90 day or 6 month coaching programs to help them live their success in a healthier, more sustainable and fulfiiled way. They pay for this privately so though they are corporate types the cards need not look 'corporate'. I want to portray the idea of transformation, vitality and re-connecting.
You can get a feel for the look I like on my new website: morvenlisk.co.uk
I want to use this logo with strapline (Re-Vitalising High Achievers) (I purchased off Logoharbor) and font/ colours (the turquoise and green).
Details to include on the card:
www.morvenlisk.co.uk
+44 7915 302618
morven@morvenlisk.co.uk
skype: morvenlisk
I'd also like to include:
Do you struggle to switch off? Want to be healthier and feel fitter? Want closer relationships? More clarity over the direction you are headed? I can help you do these things using integrated mind-body techniques. Visit morvenlisk.co.uk TODAY to apply for a FREE Breakthrough session.
BUT if that is too much text for a card I am open to advice/ammendments.
Updates
Thanks for your design - I am considering them. PLease change the wording to :

```html
<!DOCTYPE html>
<html lang="en">
<head>
<meta charset="utf-8">
<title>Morven Lisk – Business Card</title>
<link rel="stylesheet" href="https://fonts.googleapis.com/css2?family=Open+Sans:wght@400;700&display=swap">
<style>
  :root {
    --turquoise: #1aa3cf;
    --green: #5bb96a;
    --ink: #3a3a3a;
    --card: #ffffff;
    --backdrop: #eef0f1;
    --rule: #cfcfcf;
  }
  * { margin: 0; padding: 0; box-sizing: border-box; }
  html, body {
    width: 1200px; height: 720px; overflow: hidden;
    background: var(--backdrop);
    font-family: "Open Sans", Arial, sans-serif;
  }
  .canvas {
    width: 1200px; height: 720px;
    display: flex; align-items: center; justify-content: center; gap: 40px;
  }
  .card {
    position: relative;
    width: 540px; height: 310px;
    background: var(--card);
    box-shadow: 0 6px 18px rgba(0,0,0,.12);
    overflow: hidden;
  }
  .card__art { position: absolute; inset: 0; }
  .brand {
    position: absolute;
    display: flex; align-items: center; gap: 10px;
  }
  .brand__dot {
    width: 22px; height: 22px; border-radius: 50%;
    background: var(--green);
  }
  .brand__name {
    font-weight: 700; font-size: 30px; color: var(--turquoise);
    letter-spacing: .5px;
  }
  .card--front .brand { left: 40px; top: 176px; }
  .contact {
    position: absolute; right: 40px; top: 62px;
    list-style: none; text-align: right;
    color: #fff; font-size: 14px; line-height: 1;
  }
  .contact li {
    display: flex; justify-content: flex-end; align-items: center; gap: 7px;
    margin-bottom: 12px;
  }
  .contact svg { width: 13px; height: 13px; flex: none; }
  .card--back .brand { left: 34px; top: 138px; }
  .card--back .brand__name { font-size: 26px; }
  .pitch {
    position: absolute; left: 250px; top: 22px; right: 22px; bottom: 22px;
    border-left: 1px solid var(--rule);
    padding: 12px 0 0 16px;
    color: var(--ink); font-size: 13px; line-height: 1.5;
  }
  .pitch p + p { margin-top: 12px; }
  .pitch strong { font-weight: 700; }
</style>
</head>
<body>
<main class="canvas">

  <section class="card card--front" aria-label="Card front">
    <svg class="card__art" viewBox="0 0 540 310" aria-hidden="true">
      <circle cx="585" cy="-62" r="398" fill="var(--green)"/>
      <circle cx="595" cy="-74" r="382" fill="#ffffff"/>
      <circle cx="600" cy="-80" r="370" fill="var(--turquoise)"/>
    </svg>

    <div class="brand">
      <span class="brand__dot"></span>
      <span class="brand__name">Morven Lisk</span>
    </div>

    <ul class="contact">
      <li>
        <svg viewBox="0 0 16 16"><circle cx="8" cy="8" r="7.2" fill="none" stroke="#fff" stroke-width="1.4"/><path d="M5.5 4.5l1.4-.3.8 1.9-1 .7a5 5 0 0 0 2.4 2.4l.7-1 1.9.8-.3 1.4c-3.5.3-6.3-2.5-5.9-5.9z" fill="#fff"/></svg>
        <span>+44 7915 302618</span>
      </li>
      <li>
        <svg viewBox="0 0 16 16"><rect x="1.5" y="3.5" width="13" height="9" rx="1" fill="#fff"/><path d="M2 4.5l6 4.5 6-4.5" fill="none" stroke="var(--turquoise)" stroke-width="1.3"/></svg>
        <span>morven@morvenlisk.co.uk</span>
      </li>
      <li>
        <svg viewBox="0 0 16 16"><circle cx="8" cy="8" r="6.8" fill="none" stroke="#fff" stroke-width="1.4"/><ellipse cx="8" cy="8" rx="2.8" ry="6.8" fill="none" stroke="#fff" stroke-width="1.2"/><path d="M1.5 8h13" stroke="#fff" stroke-width="1.2"/></svg>
        <span>www.morvenlisk.co.uk</span>
      </li>
      <li>
        <svg viewBox="0 0 16 16"><circle cx="8" cy="8" r="7" fill="#fff"/></svg>
        <span>morvenlisk</span>
      </li>
    </ul>
  </section>

  <section class="card card--back" aria-label="Card back">
    <div class="brand">
      <span class="brand__dot"></span>
      <span class="brand__name">Morven Lisk</span>
    </div>

    <div class="pitch">
      <p>Do you struggle to switch off?<br>
      Want to be healthier and feel fitter?<br>
      Want closer relationships?<br>
      More clarity over the direction you are headed?</p>
      <p>I can help you do these things using integrated mind-body techniques.</p>
      <p>Visit <strong>morvenlisk.co.uk</strong> TODAY to apply for a FREE Breakthrough session.</p>
    </div>
  </section>

</main>
</body>
</html>
```